QVR business card

Need a business card for a company that provides instructional design and elearning development services. The website is here: http://quorvane.studio/

I'm attaching a current logo, as well as the old business card design. While I like to keep it clean, the old design is too simplistic for my liking. The only idea I want to reuse from the old design is placing industry jargon on the back of the card, just need a better way to present it. But if you have other ideas for the back--feel free to experiment.

Please use the colors complementary to the color we have on the website. Thank you!

```html
<!DOCTYPE html>
<html lang="en">
<head>
<meta charset="utf-8">
<title>QVR business card</title>
<link rel="stylesheet" href="https://fonts.googleapis.com/css2?family=Source+Sans+3:wght@400;600;700&display=swap">
<style>
  :root {
    --teal: #00aeac;
    --gold: #d8c98c;
    --white: #ffffff;
    --ink: #3b3b3b;
    --backdrop: #ecebe8;
  }
  * { margin: 0; padding: 0; box-sizing: border-box; }
  html, body {
    width: 1200px;
    height: 900px;
    overflow: hidden;
    background: var(--backdrop);
    font-family: "Source Sans 3", "Myriad Pro", sans-serif;
  }
  .card {
    position: absolute;
    background: var(--white);
    overflow: hidden;
    box-shadow: 0 6px 18px rgba(0,0,0,0.18);
  }
  .card-front { left: 77px; top: 33px; width: 589px; height: 364px; }
  .card-back  { left: 388px; top: 505px; width: 567px; height: 352px; }
  .card-bands { position: absolute; inset: 0; }
  .brand {
    position: absolute;
    left: 0; right: 0;
    display: flex;
    align-items: center;
    justify-content: center;
    gap: 16px;
  }
  .card-front .brand { top: 62px; }
  .card-back .brand { top: 58px; }
  .brand-dot {
    width: 38px; height: 38px;
    border-radius: 50%;
    background: var(--gold);
  }
  .brand-name {
    font-weight: 700;
    font-size: 64px;
    line-height: 1;
    letter-spacing: 4px;
    color: var(--teal);
  }
  .card-text {
    position: absolute;
    left: 0; right: 0;
    text-align: center;
    color: var(--white);
  }
  .holder-name {
    top: 225px;
    font-size: 19px;
    font-weight: 700;
  }
  .contact-list {
    top: 270px;
    list-style: none;
    font-size: 15.5px;
    line-height: 21px;
  }
  .contact-list b { font-weight: 700; }
  .help-heading {
    top: 198px;
    font-size: 17.5px;
    font-weight: 700;
    letter-spacing: 0.3px;
  }
  .services {
    top: 238px;
    list-style: none;
    font-size: 15.5px;
    font-weight: 600;
    line-height: 36px;
  }
  .services li span + span::before {
    content: "";
    display: inline-block;
    width: 7px; height: 7px;
    border-radius: 50%;
    background: var(--white);
    margin: 0 14px 2px;
    vertical-align: middle;
  }
</style>
</head>
<body>

<section class="card card-front">
  <svg class="card-bands" width="589" height="364" viewBox="0 0 589 364">
    <polygon fill="var(--gold)" points="0,183 400,183 383,210 0,210"/>
    <polygon fill="var(--teal)" points="413,175 589,175 589,364 0,364 0,212 379,212"/>
  </svg>
  <div class="brand">
    <span class="brand-dot"></span>
    <span class="brand-name">QVR</span>
  </div>
  <p class="card-text holder-name">Marten Holloway</p>
  <ul class="card-text contact-list">
    <li><b>Phone:</b> 555-014-2273</li>
    <li><b>Email:</b> mholloway@quorvane.studio</li>
    <li><b>Website:</b> www.quorvane.studio</li>
  </ul>
</section>

<section class="card card-back">
  <svg class="card-bands" width="567" height="352" viewBox="0 0 567 352">
    <polygon fill="var(--gold)" points="0,156 387,156 369,182 0,182"/>
    <polygon fill="var(--teal)" points="400,148 567,148 567,352 0,352 0,184 367,184"/>
  </svg>
  <div class="brand">
    <span class="brand-dot"></span>
    <span class="brand-name">QVR</span>
  </div>
  <h2 class="card-text help-heading">HOW CAN WE HELP?</h2>
  <ul class="card-text services">
    <li><span>Mobile Learning Scorm</span><span>Instructional Design Lms</span></li>
    <li><span>Moocs Elearning Html5</span><span>Adult Learning Theory</span></li>
    <li><span>Gamification Classroom</span><span>Xapi Blended Learning</span></li>
  </ul>
</section>

</body>
</html>
```